Consulting company business cards

We have a base design, but would be willing to update. We have a new logo/"tag" that needs to be added. Current business card design is attached for reference into our "style."

Industry/Entity Type

Business

Contact Information for Business Card

Should contain name and title, office number, mobile number if appropriate, e-mail, website, physical address, and company logo.

Font styles to use
Other font styles liked:
• See current card design on KorvandBCard

Colors
0455a3
85acd3
aaaaaa

Requirements
Must have
• Our colors are navy blue, gray, and a lighter blue
Nice to have
• Design that I can easily drop in new names/titles as we hire employees.

```html
<!DOCTYPE html>
<html lang="en">
<head>
<meta charset="utf-8">
<title>Braxen Business Cards</title>
<link rel="stylesheet" href="https://fonts.googleapis.com/css2?family=Source+Sans+3:wght@400;600;700&family=Open+Sans:wght@400&display=swap">
<style>
  :root {
    --stage: #000000;
    --card: #2b2d31;
    --ink: #ffffff;
    --ink-soft: #e6e7e9;
    --divider: #8a8c90;
  }
  * { margin: 0; padding: 0; box-sizing: border-box; }
  html, body { width: 1200px; height: 900px; overflow: hidden; background: var(--stage); }
  .stage { position: relative; width: 1200px; height: 900px; }
  .card {
    position: absolute; top: 271px; width: 457px; height: 281px;
    background: var(--card); border-radius: 14px;
    font-family: "Source Sans 3", "Myriad Pro", sans-serif; color: var(--ink);
  }
  .card--front { left: 137px; }
  .card--back { left: 626px; }

  .front-mark {
    position: absolute; left: 48px; top: 118px; width: 130px;
    font-size: 26px; font-weight: 700; letter-spacing: 1px; text-align: center;
  }
  .divider {
    position: absolute; left: 206px; top: 68px; width: 1px; height: 154px;
    background: linear-gradient(to bottom, transparent, var(--divider) 30%, var(--divider) 70%, transparent);
  }
  .details { position: absolute; left: 244px; top: 50px; }
  .person-name { font-size: 18px; font-weight: 600; line-height: 22px; }
  .person-title { font-size: 13px; line-height: 17px; color: var(--ink-soft); }
  .address { margin-top: 14px; font-size: 13px; line-height: 19px; color: var(--ink-soft); }
  .contact-list { list-style: none; margin-top: 16px; }
  .contact-list li {
    display: flex; align-items: center; gap: 6px;
    font-size: 13px; line-height: 19px; color: var(--ink-soft);
  }
  .contact-list svg { width: 10px; height: 10px; fill: var(--ink); flex: none; margin-left: 1px; }

  .brand { position: absolute; left: 97px; top: 100px; display: flex; align-items: center; gap: 14px; }
  .brand-name { font-size: 62px; font-weight: 700; letter-spacing: 3px; line-height: 62px; }
  .brand-dot { width: 44px; height: 44px; border-radius: 50%; background: var(--ink); }
  .tagline {
    position: absolute; left: 99px; top: 166px;
    font-family: "Open Sans", sans-serif; font-size: 12px; letter-spacing: 2.1px;
  }
  .website {
    position: absolute; left: 0; right: 0; top: 226px; text-align: center;
    font-family: "Open Sans", sans-serif; font-size: 13px; letter-spacing: 1.6px;
  }
</style>
</head>
<body>
<main class="stage">
  <section class="card card--front">
    <div class="front-mark">BRAXEN</div>
    <div class="divider"></div>
    <div class="details">
      <p class="person-name">Nadia Korvand</p>
      <p class="person-title">Office Manager</p>
      <p class="address">1187 W 54TH St Fairhaven<br>Ohio 43019</p>
      <ul class="contact-list">
        <li><svg viewBox="0 0 10 10"><path d="M2 0.5l1.6 2.2-0.9 1.1c0.6 1.3 1.4 2.1 2.5 2.6l1.1-0.9 2.2 1.6-0.8 1.9C4.5 9 1 5.5 0.1 1.3z"/></svg>555.014.2910</li>
        <li><svg viewBox="0 0 10 10"><path d="M3.5 1h3v1.5h2.5v6.5h-8v-6.5h2.5zM4.3 1.8v0.7h1.4v-0.7z"/></svg>555.014.2971</li>
        <li><svg viewBox="0 0 10 10"><path d="M0.5 2h9v0.6l-4.5 3-4.5-3zM0.5 3.6l4.5 3 4.5-3v4.4h-9z"/></svg>nkorvand@braxentech.com</li>
        <li><svg viewBox="0 0 10 10"><circle cx="5" cy="5" r="4.5"/></svg>braxentech.com</li>
      </ul>
    </div>
  </section>

  <section class="card card--back">
    <div class="brand">
      <span class="brand-name">BRAXEN</span>
      <span class="brand-dot"></span>
    </div>
    <p class="tagline">A CLOUD CONSULTING COMPANY</p>
    <p class="website">braxentech.com</p>
  </section>
</main>
</body>
</html>
```